I need a label design to go on our jars of honey. Our company is called Marrowdale Honey Co. The type of honey is called Fernlight Glen Honey. The jars are 1kg. Attached is the label size. Left hand side needs to have nutritional info... as attached. Middle section is our company name, honey type, 1kg & Whangamata, NZ. Right hand side needs to have info as per photo (raw honey etc). I would like to upload more pictures... but I’m unsure how to do this? Thanks, Carla

Target Market(s)

Honey consumers... families

Industry/Entity Type

Food Production

Colors

Designer to choose colors to be used in the design.

Requirements
Must have
• Nutritional info as per upload
• Type of honey & company name as per upload
• 1kg
• Address
Nice to have
• Similar fonts to upload.
• Possibly background image... floral or beach... very faint though.

```html
<!DOCTYPE html>
<html lang="en">
<head>
<meta charset="utf-8">
<title>Marrowdale Honey Co. – Fernlight Glen Honey Label</title>
<link href="https://fonts.googleapis.com/css2?family=Amatic+SC:wght@400;700&family=Yellowtail&family=Patrick+Hand&family=Open+Sans:wght@600;700&display=swap" rel="stylesheet">
<style>
  :root {
    --label-centre: #b73c66;
    --label-edge: #8d1d42;
    --ink: #ffffff;
    --panel-fill: rgba(255, 255, 255, 0.12);
    --rule: #ffffff;
  }
  * { margin: 0; padding: 0; box-sizing: border-box; }
  html, body { width: 1200px; height: 605px; overflow: hidden; background: var(--label-edge); }
  .label {
    position: relative;
    width: 1200px;
    height: 605px;
    color: var(--ink);
    overflow: hidden;
  }
  .label__backdrop {
    position: absolute;
    inset: 0;
    background: radial-gradient(ellipse at 50% 50%, var(--label-centre) 0%, #a72d57 55%, var(--label-edge) 100%);
  }

  /* Left column */
  .facts {
    position: absolute;
    left: 47px;
    top: 52px;
    width: 241px;
    font-family: "Open Sans", Arial, sans-serif;
    font-weight: 600;
    text-align: center;
  }
  .facts__claim { font-size: 16px; line-height: 20px; }
  .nutrition {
    margin-top: 16px;
    border: 1.5px solid var(--rule);
    text-align: left;
    height: 262px;
  }
  .nutrition__title {
    font-size: 14.5px;
    font-weight: 700;
    padding: 4px 8px 3px;
    border-bottom: 1.5px solid var(--rule);
    letter-spacing: 0.2px;
  }
  .nutrition__serving {
    font-size: 11.5px;
    font-weight: 700;
    line-height: 15px;
    padding: 5px 8px 6px;
    border-bottom: 1.5px solid var(--rule);
  }
  .nutrition table { width: 100%; border-collapse: collapse; font-size: 12px; font-weight: 700; }
  .nutrition th {
    font-size: 9.5px;
    font-weight: 600;
    text-align: left;
    padding: 6px 0 6px 8px;
    border-bottom: 1.5px solid var(--rule);
  }
  .nutrition td { padding: 2.5px 0 2.5px 8px; line-height: 18px; }
  .nutrition tbody tr:first-child td { padding-top: 7px; }
  .nutrition col.name { width: 44%; }
  .nutrition col.serve { width: 28%; }
  .facts__storage { margin-top: 14px; font-size: 15px; line-height: 19.5px; }
  .batch {
    margin-top: 18px;
    height: 93px;
    border: 1.5px solid var(--rule);
    background: var(--panel-fill);
    text-align: left;
    padding: 7px 10px;
    font-size: 14.5px;
    line-height: 19.5px;
  }

  /* Centre column */
  .brand {
    position: absolute;
    left: 350px;
    width: 500px;
    top: 62px;
    text-align: center;
  }
  .brand__name {
    font-family: "Amatic SC", "Arial Narrow", sans-serif;
    font-weight: 400;
    font-size: 58px;
    line-height: 61px;
    letter-spacing: 12px;
    padding-left: 12px;
  }
  .brand__variety {
    margin-top: 52px;
    font-family: "Yellowtail", cursive;
    font-weight: 400;
    font-size: 74px;
    line-height: 78px;
  }
  .brand__weight {
    margin-top: 68px;
    font-family: "Amatic SC", "Arial Narrow", sans-serif;
    font-size: 34px;
    line-height: 40px;
    letter-spacing: 1px;
  }
  .brand__origin {
    font-family: "Amatic SC", "Arial Narrow", sans-serif;
    font-weight: 700;
    font-size: 36px;
    line-height: 46px;
    letter-spacing: 1.5px;
  }

  /* Right column */
  .story {
    position: absolute;
    left: 876px;
    width: 300px;
    top: 74px;
    text-align: center;
    font-family: "Patrick Hand", "Comic Sans MS", cursive;
    font-size: 19px;
    line-height: 23px;
  }
  .story p + p { margin-top: 23px; }
  .story .story__faith { margin-top: 56px; }
  .story__contact { margin-top: 52px; }
  .story .story__contact { margin-top: 56px; }
</style>
</head>
<body>
<main class="label">
  <div class="label__backdrop" role="img" aria-label="Faint floral pattern of leaves and flowers over a raspberry background"></div>

  <section class="facts">
    <p class="facts__claim">100% New Zeland Honey<br>No added ingredients</p>
    <div class="nutrition">
      <h2 class="nutrition__title">NUTRITIONAL INFORMATION</h2>
      <p class="nutrition__serving">Servings per package: 100<br>Serving size: 10g</p>
      <table>
        <colgroup><col class="name"><col class="serve"><col></colgroup>
        <thead>
          <tr><th>Average Quantity</th><th>per Serving</th><th>per 100g</th></tr>
        </thead>
        <tbody>
          <tr><td>Energy</td><td>134kj</td><td>1340kj</td></tr>
          <tr><td>Protein</td><td>0.04g</td><td>0.4g</td></tr>
          <tr><td>Fat total</td><td>0g</td><td>0g</td></tr>
          <tr><td>&nbsp;- saturated</td><td>0g</td><td>0g</td></tr>
          <tr><td>Carbohydrate</td><td>7.9g</td><td>79g</td></tr>
          <tr><td>&nbsp;- sugars</td><td>7.8g</td><td>78.1g</td></tr>
          <tr><td>Sodium</td><td>1.2mg</td><td>12mg</td></tr>
        </tbody>
      </table>
    </div>
    <p class="facts__storage">Store upright in a cool, dry place.<br>No refrigeration needed.<br>Not recomended for infants<br>below the age of 12 months.</p>
    <div class="batch">
      <p>Best before:</p>
      <p>RMP:</p>
      <p>Batch No:</p>
    </div>
  </section>

  <section class="brand">
    <h1 class="brand__name">Marrowdale<br>Honey Co.</h1>
    <p class="brand__variety">Fernlight Glen<br>Honey</p>
    <p class="brand__weight">1kg</p>
    <p class="brand__origin">Whangamata, NZ</p>
  </section>

  <section class="story">
    <p>Sourced from the beautiful<br>Coromandel Pensinula.</p>
    <p>Our honey comes to you raw &amp;<br>unpasterurised, ensured it retains<br>all the natural goodness!</p>
    <p>Arohanui,<br>Rory, Carla &amp; boys</p>
    <p class="story__faith">'Marrowdale' - all thanks to God for<br>His incredible creation!</p>
    <p class="story__contact">www.marrowdalehoney.co.nz<br>24 Kowhai Lane<br>Whangamata<br>New Zeland</p>
  </section>
</main>
</body>
</html>
```